Small Business Broker Business Card Design

A business card design for a small business brokerage, which is a financial service, not unlike real estate brokerage, but for small businesses such as laundromats, pizza shops, restaurants, cleaners etc. The designs should all be simple, more conservative in nature, using the colors and font of the logo. Again, think real estate Brokerage as a business context
Contact Information for Business Card
Name: Glen R. Harlow. Title: Small Business Advisor. Email: g.harlow@bayfieldcapitalworks.example. Mobile: (555) 274-3918. Office: (555) 806-2147. www.bayfieldcapitalworks.example

```html
<!DOCTYPE html>
<html lang="en">
<head>
<meta charset="utf-8">
<title>Bayfield Capital Works – Business Card</title>
<link href="https://fonts.googleapis.com/css2?family=Montserrat:wght@400;500;600;700&display=swap" rel="stylesheet">
<style>
  :root {
    --navy: #1d3a6b;
    --green: #8bc13f;
    --white: #ffffff;
    --paper: #f7f7f7;
    --ink: #222222;
    --backdrop: #2b2b2b;
  }
  * { margin: 0; padding: 0; box-sizing: border-box; }
  html, body { width: 1200px; height: 900px; overflow: hidden; }
  body {
    background: var(--backdrop);
    font-family: "Montserrat", Arial, sans-serif;
    position: relative;
  }
  .card {
    position: absolute;
    left: 250px;
    width: 700px;
    height: 400px;
    overflow: hidden;
  }
  .card--front { top: 40px; background: var(--green); }
  .card--back  { top: 470px; background: linear-gradient(135deg, var(--white), var(--paper)); }

  /* front */
  .front-brand {
    position: absolute; inset: 0;
    display: flex; flex-direction: column; align-items: center; justify-content: center;
    gap: 10px;
  }
  .brand-row { display: flex; align-items: center; gap: 14px; }
  .brand-square { width: 30px; height: 30px; background: var(--navy); }
  .brand-name {
    color: var(--navy); font-weight: 700; font-size: 34px; letter-spacing: 1px; text-transform: uppercase;
  }
  .front-tagline {
    color: var(--white); font-weight: 600; font-size: 14px; letter-spacing: 2.5px; text-transform: uppercase;
  }

  /* back */
  .back-tab { position: absolute; right: 0; top: 30px; width: 22px; height: 34px; background: var(--green); }
  .back-band { position: absolute; left: 0; right: 0; bottom: 0; height: 16px; background: var(--green); }
  .person { position: absolute; right: 40px; top: 32px; text-align: left; }
  .person-name { font-weight: 700; font-size: 26px; color: var(--navy); }
  .person-name .surname { color: var(--green); }
  .person-title { font-size: 14px; color: var(--ink); margin-top: 2px; }

  .back-brand { position: absolute; left: 40px; top: 120px; }
  .back-brand .brand-name { font-size: 25px; }
  .back-brand .tagline { color: var(--green); font-weight: 600; font-size: 11px; letter-spacing: 1.8px; text-transform: uppercase; margin-top: 4px; }

  .mark-space {
    position: absolute; right: 60px; top: 150px; width: 150px; height: 150px; background: var(--navy);
  }

  .address { position: absolute; left: 40px; top: 222px; font-size: 15px; line-height: 1.3; color: var(--ink); }
  .contacts { position: absolute; left: 40px; top: 280px; list-style: none; font-size: 14.5px; color: var(--ink); }
  .contacts li { display: flex; align-items: center; gap: 10px; line-height: 22px; }
  .contacts svg { width: 13px; height: 13px; fill: var(--navy); flex: none; }
</style>
</head>
<body>

<section class="card card--front">
  <div class="front-brand">
    <div class="brand-row">
      <span class="brand-square"></span>
      <span class="brand-name">Bayfield Capital Works, Inc</span>
    </div>
    <p class="front-tagline">Confidently buy or sell a local business today</p>
  </div>
</section>

<section class="card card--back">
  <div class="back-tab"></div>

  <div class="person">
    <p class="person-name">Glen R. <span class="surname">Harlow</span></p>
    <p class="person-title">Small Business Advisor</p>
  </div>

  <div class="back-brand">
    <p class="brand-name">Bayfield Capital Works, Inc</p>
    <p class="tagline">Confidently buy or sell a local business today</p>
  </div>

  <div class="mark-space"></div>

  <p class="address">418 Harbor Point Ave<br>Riverton, Florida 30012</p>

  <ul class="contacts">
    <li>
      <svg viewBox="0 0 16 16"><path d="M2 6c0-2 2-3 6-3s6 1 6 3v1h-3V6H5v1H2zM4 8h8l2 6H2z"/></svg>
      (555) 806-2147
    </li>
    <li>
      <svg viewBox="0 0 16 16"><path d="M4 1l3 3-2 2c1 2 3 4 5 5l2-2 3 3-2 3C7 15 1 9 1 3z"/></svg>
      (555) 274-3918
    </li>
    <li>
      <svg viewBox="0 0 16 16"><path d="M1 3h14v10H1zM2 4l6 5 6-5"/></svg>
      g.harlow@bayfieldcapitalworks.example
    </li>
    <li>
      <svg viewBox="0 0 16 16"><circle cx="8" cy="8" r="7"/></svg>
      www.bayfieldcapitalworks.example
    </li>
  </ul>

  <div class="back-band"></div>
</section>

</body>
</html>
```